Business Card for Coastal Tundrabridge Advisory

We need a business card for Coastal Tundrabridge Advisory. The company website address is provided below. The company logo is attached. We provide specialized permafrost services to the mining, transportation, and oil & gas industries. The card should be prepared for:
Matthias Korhonen, PhD.
Coastal Tundrabridge Advisory
PO Box 418259
Quillwater, Alaska 99642
Direct: +1-907-555-0143
Email: mkorhonen@tundrabridgeadvisory.example
Website: www.coastaltundrabridgeadvisory.example

```html
<!DOCTYPE html>
<html lang="en">
<head>
<meta charset="utf-8">
<title>Coastal Tundrabridge Advisory – Business Card</title>
<link href="https://fonts.googleapis.com/css2?family=Arimo:wght@400;700&family=Jost:wght@500&display=swap" rel="stylesheet">
<style>
  :root {
    --backdrop: #dcdcdc;
    --paper: #f5f5f5;
    --ink: #14191f;
    --ink-soft: #555a60;
    --night: #111820;
    --steel: #5b5c5e;
    --frost: #ffffff;
    --mist: #d6d8db;
  }
  html, body {
    margin: 0;
    padding: 0;
    width: 1200px;
    height: 1040px;
    overflow: hidden;
    background: var(--backdrop);
  }
  .canvas {
    position: relative;
    width: 1200px;
    height: 1040px;
  }
  .card {
    position: absolute;
    left: 278px;
    width: 644px;
    height: 368px;
    border-radius: 16px;
    overflow: hidden;
    box-sizing: border-box;
  }
  .card--front { top: 128px; background: var(--paper); color: var(--ink); font-family: "Arimo", Arial, sans-serif; }
  .card--back { top: 572px; background: var(--night); color: var(--frost); }

  .brand-name {
    font-family: "Jost", "Futura", sans-serif;
    font-weight: 500;
    text-transform: uppercase;
    letter-spacing: 0.12em;
    margin: 0;
  }
  .card--front .brand-name {
    position: absolute;
    right: 46px;
    top: 40px;
    font-size: 17px;
    line-height: 21px;
    text-align: right;
    color: var(--ink);
  }

  .holder { position: absolute; left: 43px; top: 204px; }
  .holder__name { margin: 0; font-size: 24px; font-weight: 700; line-height: 28px; }
  .holder__degree { font-size: 18px; }
  .holder__title { margin: 1px 0 0 2px; font-size: 16px; color: var(--ink-soft); }

  .divider {
    position: absolute;
    left: 43px;
    right: 46px;
    top: 258px;
    height: 0;
    border-top: 1px solid var(--ink);
  }

  .contact {
    position: absolute;
    left: 44px;
    top: 265px;
    margin: 0;
    padding: 0;
    list-style: none;
    font-size: 16px;
    line-height: 20px;
  }
  .contact li { display: flex; align-items: center; gap: 8px; }
  .contact svg { width: 13px; height: 13px; fill: var(--ink); }

  .address {
    position: absolute;
    right: 46px;
    top: 265px;
    margin: 0;
    font-style: normal;
    font-size: 16px;
    line-height: 20px;
    text-align: right;
  }

  .band { position: absolute; left: 0; bottom: 0; width: 644px; height: 44px; }
  .band__url {
    position: absolute;
    right: 30px;
    bottom: 12px;
    font-size: 16px;
    color: var(--frost);
  }

  .card--back .brand-name {
    position: absolute;
    left: 0;
    right: 0;
    top: 130px;
    text-align: center;
    font-size: 34px;
    line-height: 44px;
    letter-spacing: 0.14em;
    color: var(--frost);
  }
  .card--back .site {
    position: absolute;
    left: 0;
    right: 0;
    top: 318px;
    text-align: center;
    font-family: "Arimo", Arial, sans-serif;
    font-size: 16px;
    color: var(--mist);
  }
</style>
</head>
<body>
<main class="canvas">

  <section class="card card--front" aria-label="Business card front">
    <p class="brand-name">Coastal Tundrabridge<br>Advisory</p>

    <div class="holder">
      <h1 class="holder__name">Matthias Korhonen, <span class="holder__degree">PhD.</span></h1>
      <p class="holder__title">President</p>
    </div>

    <div class="divider"></div>

    <ul class="contact">
      <li>
        <svg viewBox="0 0 24 24" aria-hidden="true"><path d="M6.6 10.8a15.1 15.1 0 0 0 6.6 6.6l2.2-2.2a1 1 0 0 1 1-.25 11.4 11.4 0 0 0 3.6.57 1 1 0 0 1 1 1V20a1 1 0 0 1-1 1A17 17 0 0 1 3 4a1 1 0 0 1 1-1h3.5a1 1 0 0 1 1 1c0 1.25.2 2.45.57 3.57a1 1 0 0 1-.25 1z"/></svg>
        <span>+1-907-555-0143</span>
      </li>
      <li>
        <svg viewBox="0 0 24 24" aria-hidden="true"><path d="M2 5h20v14H2z M3.5 6.5 12 12.5l8.5-6" fill="none" stroke="#14191f" stroke-width="0"/><path d="M2 6.2V19h20V6.2l-10 7z"/><path d="M2.6 5h18.8L12 11.6z"/></svg>
        <span>mkorhonen@tundrabridgeadvisory.example</span>
      </li>
    </ul>

    <address class="address">PO Box 418259<br>Quillwater, Alaska 99642</address>

    <svg class="band" viewBox="0 0 644 44" aria-hidden="true">
      <path d="M0 36 H300 L326 2 H644 V44 H0 Z" fill="#111820"/>
      <path d="M0 8 H318 L302 28 H0 Z" fill="#5b5c5e"/>
      <path d="M0 31 H300 L322 4" fill="none" stroke="#f5f5f5" stroke-width="2"/>
    </svg>
    <span class="band__url">coastaltundrabridgeadvisory.example</span>
  </section>

  <section class="card card--back" aria-label="Business card back">
    <p class="brand-name">Coastal Tundrabridge<br>Advisory</p>
    <p class="site">www.coastaltundrabridgeadvisory.example</p>
  </section>

</main>
</body>
</html>
```